Birchline Septic Solutions

Would like to see some single sided ones but would also like to see some double sided with one sided only being the logo. Owners name is Colin Vandro. Phone number is 555-214-0387
Services are pumping, inspections, installs, and repairs

Contact Information for Business Card

555-241-0387 Colin Vandro Harlow Creek, OH

```html
<!DOCTYPE html>
<html lang="en">
<head>
<meta charset="utf-8">
<title>Birchline Septic Solutions – Business Cards</title>
<link rel="stylesheet" href="https://fonts.googleapis.com/css2?family=Open+Sans:wght@400;600;700&display=swap">
<style>
  :root {
    --page-bg: #262626;
    --card-bg: #212125;
    --teal: #26bfb8;
    --white: #ffffff;
    --muted: #e6e6e6;
    --divider: #9a9a9a;
  }
  * { box-sizing: border-box; margin: 0; padding: 0; }
  html, body {
    width: 1200px; height: 779px; overflow: hidden;
    background: var(--page-bg);
    font-family: "Open Sans", Arial, sans-serif;
  }
  .sheet {
    position: relative; width: 1200px; height: 779px;
    display: flex; align-items: center; justify-content: center; gap: 40px;
  }
  .card {
    position: relative; width: 540px; height: 309px;
    background: var(--card-bg);
    box-shadow: 0 12px 30px rgba(0,0,0,.55);
    overflow: hidden;
  }
  /* Front: name only */
  .card--front { display: flex; align-items: center; justify-content: center; }
  .wordmark {
    display: flex; align-items: center; gap: 12px;
    color: var(--white); font-weight: 700; letter-spacing: .5px;
  }
  .wordmark__square { width: 14px; height: 14px; background: var(--teal); flex: none; }
  .card--front .wordmark { font-size: 30px; }
  .card--front .wordmark__text { line-height: 1.15; text-align: left; max-width: 300px; }

  /* Back: contact side */
  .card--back .wordmark {
    position: absolute; left: 58px; top: 88px; font-size: 19px;
  }
  .card--back .wordmark__text { max-width: 170px; line-height: 1.2; }
  .divider {
    position: absolute; left: 268px; top: 62px; width: 1px; height: 110px;
    background: var(--divider);
  }
  .contact { position: absolute; left: 292px; top: 72px; color: var(--white); }
  .contact__name { font-size: 27px; font-weight: 700; line-height: 1.1; }
  .contact__first { color: var(--teal); }
  .contact__city, .contact__phone { font-size: 15px; color: var(--muted); margin-top: 6px; }
  .contact__phone { display: flex; align-items: center; gap: 7px; }
  .contact__phone svg { width: 13px; height: 13px; fill: var(--teal); }

  .services-tag {
    position: absolute; left: 292px; top: 212px;
    padding: 2px 18px; border-radius: 50%;
    background: var(--teal); border: 2px solid var(--white);
    color: var(--white); font-size: 14px; font-weight: 600;
  }
  .services-band {
    position: absolute; left: 0; right: 0; bottom: 20px; height: 36px;
    background: var(--teal);
    display: flex; align-items: center; justify-content: center; gap: 14px;
    color: var(--white); font-size: 15px; font-weight: 600;
  }
  .services-band li { list-style: none; display: flex; align-items: center; gap: 6px; }
  .services-band li::before {
    content: ""; width: 8px; height: 8px; border-radius: 50%; background: var(--white);
  }
</style>
</head>
<body>
<main class="sheet">
  <section class="card card--front" aria-label="Card front">
    <div class="wordmark">
      <span class="wordmark__square"></span>
      <span class="wordmark__text">Birchline Septic Solutions</span>
    </div>
  </section>

  <section class="card card--back" aria-label="Card back">
    <div class="wordmark">
      <span class="wordmark__square"></span>
      <span class="wordmark__text">Birchline Septic Solutions</span>
    </div>
    <div class="divider"></div>
    <div class="contact">
      <p class="contact__name"><span class="contact__first">Colin</span> Vandro</p>
      <p class="contact__city">Harlow Creek, OH</p>
      <p class="contact__phone">
        <svg viewBox="0 0 24 24" aria-hidden="true"><path d="M6.6 10.8a15.1 15.1 0 0 0 6.6 6.6l2.2-2.2c.3-.3.7-.4 1-.2 1.1.4 2.3.6 3.6.6.6 0 1 .4 1 1V20c0 .6-.4 1-1 1A17 17 0 0 1 3 4c0-.6.4-1 1-1h3.5c.6 0 1 .4 1 1 0 1.3.2 2.5.6 3.6.1.3 0 .7-.2 1z"/></svg>
        555-241-0387
      </p>
    </div>
    <span class="services-tag">SERVICES</span>
    <ul class="services-band">
      <li>Pumping</li>
      <li>Inspections</li>
      <li>Installs</li>
      <li>And Repairs</li>
    </ul>
  </section>
</main>
</body>
</html>
```